Automotive component supplier needs a business card design

We need a business card design for our company called Velran Global Components Ltd based in the UK. We are a supplier of interior and exterior components to premium car manufacturers such as Corvel Ashby, Hadley Fenn, Marquist and Tavarelli. We would like to see a modern business card design that uses the colour blue.

Target Market(s)

Premium automotive car manufacturers.

Industry/Entity Type

Automotive

Contact Information for Business Card

Company Name : Velran Global Components Limited
Address: 17 Marlow Yard, Upper Heath, Warwick, CV31 8QL, United Kingdom
Web Address : www.velrancomponents-example.co.uk

Font styles to use
Other font styles liked:
• Helvetica

Colors
3176b5
0255a3
85acd3
cfdeed
cee9f5
85cae6
34a6d7
0692cd
9bcb3c

Requirements
Must have
• Clear company logo and a mixture of blue colours.
Nice to have
• A high quality modern image.
Should not have
• Multiple colours.

```html
<!DOCTYPE html>
<html lang="en">
<head>
<meta charset="utf-8">
<title>Velran Global Components – Business Card</title>
<link rel="stylesheet" href="https://fonts.googleapis.com/css2?family=Titillium+Web:wght@400;600;700&display=swap">
<style>
  :root {
    --brand-blue: #0a8fcf;
    --brand-green: #9bcb3c;
    --card-white: #ffffff;
    --text-grey: #555b60;
    --rule-grey: #8a8f94;
    --backdrop: #2a2a2a;
  }
  * { margin: 0; padding: 0; box-sizing: border-box; }
  html, body {
    width: 1200px; height: 987px; overflow: hidden;
    background: var(--backdrop);
    font-family: "Titillium Web", Arial, sans-serif;
  }
  .canvas { position: relative; width: 1200px; height: 987px; }

  .card {
    position: absolute; left: 293px; width: 615px; height: 352px;
    box-shadow: 0 4px 14px rgba(0,0,0,.45);
  }
  .card--front { top: 130px; background: var(--card-white); }
  .card--back { top: 505px; background: var(--brand-blue); }

  .edge-strip {
    position: absolute; left: 0; top: 0; width: 35px; height: 100%;
    background: var(--brand-blue);
  }
  .edge-marker {
    position: absolute; left: 0; top: 161px; width: 35px; height: 40px;
    background: var(--brand-green);
    border-top: 3px solid var(--card-white);
    border-bottom: 3px solid var(--card-white);
    border-right: 3px solid var(--card-white);
    border-radius: 0 6px 6px 0;
  }

  .wordmark { position: absolute; font-weight: 700; line-height: 1; }
  .wordmark__name { display: block; letter-spacing: 1px; }
  .wordmark__sub { display: block; letter-spacing: 1.2px; }

  .card--front .wordmark { left: 74px; top: 44px; color: var(--brand-blue); }
  .card--front .wordmark__name { font-size: 58px; }
  .card--front .wordmark__sub { font-size: 15px; margin-top: 4px; }

  .card--back .wordmark {
    left: 0; right: 0; top: 118px; text-align: center; color: var(--card-white);
  }
  .card--back .wordmark__name { font-size: 84px; }
  .card--back .wordmark__sub { font-size: 19px; margin-top: 6px; }

  .person { position: absolute; left: 74px; top: 155px; }
  .person__name {
    font-size: 22px; font-weight: 700; color: var(--brand-blue);
    letter-spacing: .5px; line-height: 1.2;
  }
  .person__role { font-size: 15px; color: var(--brand-green); line-height: 1.4; }

  .address {
    position: absolute; left: 74px; top: 212px;
    font-size: 15px; line-height: 22px; color: var(--text-grey); font-style: normal;
  }

  .contacts {
    position: absolute; left: 74px; top: 270px;
    display: flex; align-items: stretch;
    font-size: 15px; color: var(--text-grey);
  }
  .contacts__group { display: flex; flex-direction: column; gap: 3px; }
  .contacts__rule { width: 1px; background: var(--rule-grey); margin: 0 16px 0 24px; }
  .contact { display: flex; align-items: center; gap: 8px; line-height: 21px; }
  .contact svg { width: 14px; height: 14px; flex: none; fill: var(--brand-blue); }
</style>
</head>
<body>
<main class="canvas">

  <section class="card card--front" aria-label="Business card front">
    <div class="edge-strip"></div>
    <div class="edge-marker"></div>

    <div class="wordmark">
      <span class="wordmark__name">VELRAN</span>
      <span class="wordmark__sub">GLOBAL COMPONENTS</span>
    </div>

    <div class="person">
      <p class="person__name">DANIEL HART</p>
      <p class="person__role">CEO/Founder</p>
    </div>

    <address class="address">
      17 Marlow Yard, Upper Heath<br>
      Warwick, CV31 8QL, United Kingdom
    </address>

    <div class="contacts">
      <div class="contacts__group">
        <span class="contact">
          <svg viewBox="0 0 24 24" aria-hidden="true"><path d="M6.6 10.8a15.1 15.1 0 0 0 6.6 6.6l2.2-2.2a1 1 0 0 1 1-.25 11.4 11.4 0 0 0 3.6.57 1 1 0 0 1 1 1V20a1 1 0 0 1-1 1A17 17 0 0 1 3 4a1 1 0 0 1 1-1h3.5a1 1 0 0 1 1 1c0 1.25.2 2.45.57 3.57a1 1 0 0 1-.25 1z"/></svg>
          555 014 2738
        </span>
        <span class="contact">
          <svg viewBox="0 0 24 24" aria-hidden="true"><path d="M7 1h10a2 2 0 0 1 2 2v18a2 2 0 0 1-2 2H7a2 2 0 0 1-2-2V3a2 2 0 0 1 2-2zm0 3v14h10V4zm5 15.2a1 1 0 1 0 0 2 1 1 0 0 0 0-2z"/></svg>
          555 019 4360
        </span>
      </div>
      <div class="contacts__rule"></div>
      <div class="contacts__group">
        <span class="contact">
          <svg viewBox="0 0 24 24" aria-hidden="true"><path d="M2 5h20v14H2zm2 2v.4l8 5.3 8-5.3V7zm0 2.8V17h16V9.8l-8 5.3z"/></svg>
          daniel@velrancomponents-example.co.uk
        </span>
        <span class="contact">
          <svg viewBox="0 0 24 24" aria-hidden="true"><path d="M12 2a10 10 0 1 0 0 20 10 10 0 0 0 0-20zm-1 17.9A8 8 0 0 1 4.2 10.5L9 15.3v1a2 2 0 0 0 2 2zm6.9-2.5A2 2 0 0 0 16 16h-1v-3a1 1 0 0 0-1-1H8v-2h2a1 1 0 0 0 1-1V7h2a2 2 0 0 0 2-2v-.4a8 8 0 0 1 2.9 12.8z"/></svg>
          www.velrancomponents-example.co.uk
        </span>
      </div>
    </div>
  </section>

  <section class="card card--back" aria-label="Business card back">
    <div class="wordmark">
      <span class="wordmark__name">VELRAN</span>
      <span class="wordmark__sub">GLOBAL COMPONENTS</span>
    </div>
  </section>

</main>
</body>
</html>
```